Business Card Design

We need a design for business cards for our company. We have a logo. We teach EMT's and we are based out of Virginia. The information that will need to add would be, name, title, phone number, email, address. On the back of the business card would be "We help you, help others"

Target Market(s)

People that want to become EMT's

Colors

Designer to choose colors to be used in the design.

Requirements
Must have
• company logo

```html
<!DOCTYPE html>
<html lang="en">
<head>
<meta charset="utf-8">
<title>Rescue Ready Academy – Business Card</title>
<link href="https://fonts.googleapis.com/css2?family=Montserrat:wght@400;600&family=Lato:wght@400;700&display=swap" rel="stylesheet">
<style>
  :root {
    --page-bg: #1c1c1e;
    --card-navy: #1d2436;
    --card-navy-deep: #161c2a;
    --accent-red: #e8283f;
    --steel-grey: #7d8b98;
    --text-light: #e6e9ee;
    --pattern-tone: #2c3649;
  }
  * { margin: 0; padding: 0; box-sizing: border-box; }
  html, body {
    width: 1200px; height: 900px; overflow: hidden;
    background: var(--page-bg);
  }
  .canvas { position: relative; width: 1200px; height: 900px; }

  .card {
    position: absolute; left: 250px; width: 700px; height: 400px;
    background: linear-gradient(160deg, var(--card-navy) 0%, var(--card-navy-deep) 100%);
    overflow: hidden;
    box-shadow: 0 14px 30px rgba(0,0,0,0.55);
  }
  .card--front { top: 35px; }
  .card--back { top: 465px; }

  .pattern-area {
    position: absolute; top: 0; right: 0; width: 48%; height: 100%;
    background:
      radial-gradient(ellipse 70% 55% at 75% 25%, var(--pattern-tone) 0%, rgba(44,54,73,0) 100%),
      radial-gradient(ellipse 50% 40% at 60% 75%, rgba(44,54,73,0.7) 0%, rgba(44,54,73,0) 100%);
  }

  .brand {
    position: absolute; display: flex; align-items: center; gap: 12px;
    white-space: nowrap;
    font-family: "Montserrat", sans-serif; font-weight: 600;
    color: var(--accent-red); letter-spacing: 1px; text-transform: uppercase;
  }
  .brand__dot {
    flex: none; width: 16px; height: 16px; border-radius: 50%; background: var(--accent-red);
  }
  .card--front .brand { left: 110px; top: 160px; font-size: 34px; }
  .card--back .brand { left: 170px; top: 70px; font-size: 28px; }

  .tagline {
    position: absolute; right: 110px; bottom: 110px;
    font-family: "Montserrat", sans-serif; font-weight: 400;
    font-size: 15px; letter-spacing: 1px; color: var(--text-light);
  }

  .contact {
    position: absolute; left: 50px; bottom: 55px;
    font-family: "Lato", sans-serif; color: var(--text-light);
  }
  .contact__name {
    font-size: 22px; letter-spacing: 0.5px; color: var(--accent-red); text-transform: uppercase;
  }
  .contact__name strong { font-weight: 700; }
  .contact__name span { font-weight: 400; }
  .contact__title { font-size: 15px; font-weight: 700; margin-bottom: 16px; }
  .contact__row {
    display: flex; align-items: center; gap: 12px; font-size: 15px; margin-top: 6px;
  }
  .contact__row svg { width: 16px; height: 16px; }

  .band { position: absolute; left: 0; bottom: 0; width: 700px; height: 90px; }
</style>
</head>
<body>
<main class="canvas">

  <section class="card card--front" aria-label="Card front">
    <div class="pattern-area" role="img" aria-label="Faint medical cross pattern"></div>
    <div class="brand"><span class="brand__dot"></span>Rescue Ready Academy</div>
    <p class="tagline">WE HELP YOU, HELP OTHERS</p>
  </section>

  <section class="card card--back" aria-label="Card back">
    <div class="pattern-area" role="img" aria-label="Faint medical cross pattern"></div>
    <div class="brand"><span class="brand__dot"></span>Rescue Ready Academy</div>

    <div class="contact">
      <p class="contact__name"><strong>Dana</strong> <span>Whitfield</span></p>
      <p class="contact__title">Founder / Director</p>
      <p class="contact__row">
        <svg viewBox="0 0 24 24" aria-hidden="true"><path fill="#e8283f" d="M6.6 10.8a15.1 15.1 0 0 0 6.6 6.6l2.2-2.2c.3-.3.7-.4 1-.2 1.1.4 2.3.6 3.6.6.6 0 1 .4 1 1V20c0 .6-.4 1-1 1C10.6 21 3 13.4 3 4c0-.6.4-1 1-1h3.5c.6 0 1 .4 1 1 0 1.3.2 2.5.6 3.6.1.3 0 .7-.2 1z"/></svg>
        +1 540 555 0134
      </p>
      <p class="contact__row">
        <svg viewBox="0 0 24 24" aria-hidden="true"><path d="M3 5h18v14H3z M3 5l9 7 9-7" fill="none" stroke="#e8283f" stroke-width="2"/></svg>
        info@rescuereadyacademy.com
      </p>
    </div>

    <svg class="band" viewBox="0 0 700 90" preserveAspectRatio="none" aria-hidden="true">
      <path d="M0 78 H545 Q556 78 559 68 L562 60 Q565 52 576 52 H700 V90 H0 Z" fill="var(--steel-grey)"/>
      <path d="M568 56 Q568 36 588 32 L700 10 V52 H572 Z" fill="var(--accent-red)"/>
    </svg>
  </section>

</main>
</body>
</html>
```